Local Chiropractoc needs Modern Website

This website needs to have an upscale look with a very modern feel.

This is for a home page psd layout and an interior page psd file so 2 files total

Below is the information and websites to reference

Add Logo that is attached.

Build a color scheme similar to this website image titled "chiro-1" using the golds, whites, blacks and browns from the color of the logo

I want to see a light background so it makes the images and logo stick out

Must Include these pages in a horizontal menu bar in this order:
Home, Why Fair Ridge?, How Chiropractic Helps, Ask the Doctor, Work Place Wellness, Request an Appointment, Blog, Contact Us

Please add the following social media logos to the top and footer of the website: Chatterly, Plexo+, Vidzio

Build a "classy looking" Make An Appointment Button into the header with the contact info below

Phone Number:
555-014-2297

Address:
4172 North Maple Blvd, Suite #7
Harlow Springs, FL 32990

This website needs 4 rotating banners. Please reference a layout similar to this for the banners: http://hollowpinespine.com/. However design it nicer than this website

Below are the description for each banner

Rotating Banner #1
Use Image: Patients are Saying
Add a line of text: "What our Patients are Saying"

Rotating Banner #2
Use Image: Becoming a Patient
Add a line of text: "Interested in Becoming a Patient"

Rotating Banner #3
Use Image: Dinner with Doctor
Add a line of text: "Win A free Dinner with Dr. Hollins"

Rotating Banner #4
Use Image: Chatterly
Add a line of text: Follow us on Chatterly
Bullet point these 4 lines underneath the "Follow us on Chatterly" text:
- Cutting Edge Health News
- Healthy Recipes
- Newest Health Products
- Clinic Events

I'd like to see a free consultation box similar to the "chiro-1" image. Fields to include are: First Name, Last Name, Phone Number, Comments

For the body, please fill it with latin text. Please design a professional 2 column layout similar to the www.hollowpinespine.com website. (DO NOT COPY THIS WEBSITE, USE IT AS REFERENCE)

In the left column include in this order:
Video
Rate us on Plexo Button, Find us on Chatterly Button
Welcome Letter

In the right column include this:

Office Hours
Monday: 8:00-11:00, 2:00-5:00
Tuesday: 8:30-11:00, 2:00-5:30
Wednesday: 8:00-11:00, 2:00-5:00
Thursday: 10:00-12:00, 2:30-5:00
Friday: 8:00-10:00, 1:00-5:00
Saturday: Closed
Sunday: Closed

Patient Testimonials
Fill with a latin text testimonial. This spot will rotate different testimonials

For the footer please design something similar to the layout of this: http://www.tidewellhealer.com/

Also include in the Footer: Powered by Crestline Pixel Group

```html
<!DOCTYPE html>
<html lang="en">
<head>
<meta charset="utf-8">
<title>Fair Ridge Chiropractic</title>
<link href="https://fonts.googleapis.com/css2?family=Raleway:wght@300;400;600;700&family=Open+Sans:wght@400;600&display=swap" rel="stylesheet">
<style>
:root{
  --gold:#b78d47;
  --gold-light:#d6b272;
  --gold-pale:#efe2c6;
  --brown:#3b2b1c;
  --brown-mid:#5a4330;
  --ink:#333;
  --muted:#777;
  --page:#f3f1ec;
  --white:#fff;
  --red:#c9322a;
  --blue:#3b5a98;
}
*{box-sizing:border-box;margin:0;padding:0}
html,body{width:857px;height:1200px;overflow:hidden}
body{background:var(--page);font-family:"Open Sans",Arial,sans-serif;color:var(--ink);font-size:9px;line-height:1.5}
.page{width:760px;margin:0 auto;background:var(--white);height:1050px;position:relative}

/* header */
.site-header{height:93px;display:flex;justify-content:space-between;align-items:center;padding:0 16px 0 28px}
.brand{display:flex;align-items:center;gap:10px}
.brand-mark{width:24px;height:24px;background:var(--brown);flex:none}
.brand-name{font-family:"Raleway",sans-serif;font-weight:700;color:var(--brown);font-size:18px;line-height:1.1;letter-spacing:1px}
.header-contact{text-align:right;font-size:9px;color:var(--muted)}
.header-contact .address{line-height:1.4}
.header-actions{display:flex;align-items:center;justify-content:flex-end;gap:8px;margin:6px 0 4px}
.social{display:flex;gap:4px}
.social span{font-family:"Raleway",sans-serif;font-weight:600;font-size:8px;color:var(--white);background:var(--gold);padding:2px 5px}
.btn-appointment{font-family:"Raleway",sans-serif;font-weight:600;font-size:10px;color:var(--white);background:linear-gradient(var(--gold-light),var(--gold));border:1px solid #9a7538;padding:5px 14px;border-radius:2px}
.phone{font-family:"Raleway",sans-serif;font-weight:700;font-size:15px;color:var(--gold)}

/* nav */
.main-nav{height:20px;background:var(--brown);border-top:2px solid var(--gold);display:flex;justify-content:center;gap:22px;align-items:center}
.main-nav a{color:var(--gold-pale);text-decoration:none;font-family:"Raleway",sans-serif;font-weight:600;font-size:8.5px}

/* hero */
.hero{height:327px;position:relative;background:linear-gradient(100deg,#6f6a4e 0%,#a88a63 35%,#e0b990 55%,#c99a6e 75%,#7e7150 100%)}
.hero-caption{position:absolute;left:40px;top:160px;background:rgba(30,20,12,.7);padding:14px 22px;color:var(--white);font-family:"Raleway",sans-serif}
.hero-caption .line1{font-weight:300;font-size:22px}
.hero-caption .line2{font-weight:400;font-size:34px;line-height:1}
.hero-caption small{display:block;font-size:8px;opacity:.8;margin-top:6px;font-family:"Open Sans",sans-serif}
.dots{position:absolute;bottom:10px;left:50%;transform:translateX(-50%);display:flex;gap:6px}
.dots i{width:8px;height:8px;border-radius:50%;background:rgba(255,255,255,.55)}
.dots i.on{background:var(--gold)}

/* body */
.content{display:flex;gap:24px;padding:12px 16px 0}
.main-col{width:414px}
.side-col{width:290px}
.video{height:290px;position:relative;background:linear-gradient(135deg,#d8c5ab,#b99b7c 50%,#8a6e55)}
.video svg{position:absolute;left:50%;top:50%;transform:translate(-50%,-50%)}
.video-bar{position:absolute;left:0;right:0;bottom:0;height:18px;background:rgba(0,0,0,.6)}
.video-bar::after{content:"";position:absolute;left:30px;right:60px;top:8px;height:3px;background:#888}
.share-buttons{display:flex;gap:14px;margin:14px 0 18px}
.share-buttons a{flex:1;height:40px;display:flex;align-items:center;gap:10px;padding:0 14px;color:var(--white);text-decoration:none;font-family:"Raleway",sans-serif;font-weight:600;font-size:14px}
.share-buttons a i{width:22px;height:22px;background:rgba(255,255,255,.9)}
.btn-rate{background:var(--red)}
.btn-find{background:var(--blue)}
.welcome h1{font-family:"Raleway",sans-serif;font-weight:600;font-size:17px;color:var(--brown);margin-bottom:6px}
.welcome p{font-size:8px;color:var(--muted);margin-bottom:6px;line-height:1.55}
.welcome p.lead{color:var(--gold);font-size:8.5px}

.consult{background:var(--brown);padding:12px 16px;height:255px}
.consult h2{font-family:"Raleway",sans-serif;font-weight:700;font-size:15px;color:var(--gold-light);text-align:center;letter-spacing:1px;border:1px solid var(--gold);padding:3px 0}
.consult h2 span{display:block;font-weight:400;font-size:12px;color:var(--white);letter-spacing:0}
.field{background:var(--white);height:20px;margin-top:8px;padding:3px 6px;color:#999;font-size:8px}
.field.area{height:44px}
.btn-book{display:block;width:90px;margin:9px auto 0;text-align:center;background:var(--gold);color:var(--white);font-family:"Raleway",sans-serif;font-weight:700;font-size:10px;padding:4px 0}

.panel{margin-top:10px;background:var(--gold-pale)}
.panel h3{background:linear-gradient(var(--gold-light),var(--gold));color:var(--white);font-family:"Raleway",sans-serif;font-weight:600;font-size:13px;padding:4px 12px}
.hours{width:100%;border-collapse:collapse;font-size:8.5px}
.hours td{padding:3px 12px;border-bottom:1px solid #e0cfa8}
.hours td:last-child{text-align:right}
.testimonial{padding:6px 12px;font-size:8px;color:var(--muted)}
.testimonial cite{display:block;text-align:right;font-style:italic;color:var(--brown);margin-top:3px}

/* footer */
.footer-band{position:absolute;top:1050px;left:0;width:857px;height:80px;background:linear-gradient(90deg,#c7a263,#e2c58d 50%,#c7a263)}
.footer-band svg{position:absolute;top:-20px;left:0}
.footer-inner{width:760px;margin:0 auto;display:flex;justify-content:space-between;align-items:center;height:80px;padding:0 28px;position:relative}
.footer-address{font-size:9px;color:var(--brown);line-height:1.5}
.footer-address strong{font-family:"Raleway",sans-serif;font-size:11px}
.footer-brand .brand-name{font-size:16px}
.footer-bar{position:absolute;top:1130px;left:0;width:857px;height:70px;background:var(--brown)}
.footer-bar .inner{width:760px;margin:0 auto;padding:12px 28px;color:var(--gold-pale);font-size:8px}
.footer-nav{display:flex;gap:6px;flex-wrap:wrap}
.footer-nav a{color:var(--gold-pale);text-decoration:none}
.footer-nav a+a::before{content:"|";margin-right:6px;color:var(--gold)}
.footer-row{display:flex;justify-content:space-between;align-items:center;margin-top:8px}
</style>
</head>
<body>
<div class="page">
  <header class="site-header">
    <div class="brand">
      <span class="brand-mark"></span>
      <span class="brand-name">FAIR RIDGE<br>CHIROPRACTIC</span>
    </div>
    <div class="header-contact">
      <div class="address">4172 North Maple Blvd, Suite #7<br>Harlow Springs, FL 32990</div>
      <div class="header-actions">
        <div class="social"><span>Chatterly</span><span>Plexo+</span><span>Vidzio</span></div>
        <a class="btn-appointment">Make an Appointment</a>
      </div>
      <div class="phone">555-014-2297</div>
    </div>
  </header>

  <nav class="main-nav">
    <a>Home</a><a>Why Fair Ridge?</a><a>How Chiropractic Helps</a><a>Ask the Doctor</a><a>Work Place Wellness</a><a>Request an Appointment</a><a>Blog</a><a>Contact Us</a>
  </nav>

  <section class="hero" role="img" aria-label="Banner photo of a smiling family of patients">
    <div class="hero-caption">
      <div class="line1">What our Patients</div>
      <div class="line2">are Saying</div>
      <small>Lorem ipsum dolor sit amet, consectetur adipiscing elit sed do.</small>
    </div>
    <div class="dots"><i class="on"></i><i></i><i></i><i></i></div>
  </section>

  <div class="content">
    <main class="main-col">
      <div class="video" role="img" aria-label="Video still of a chiropractic adjustment">
        <svg width="60" height="42" viewBox="0 0 60 42"><rect width="60" height="42" rx="8" fill="rgba(0,0,0,.7)"/><path d="M24 12 L40 21 L24 30Z" fill="#fff"/></svg>
        <div class="video-bar"></div>
      </div>
      <div class="share-buttons">
        <a class="btn-rate"><i></i>Rate us on Plexo</a>
        <a class="btn-find"><i></i>Find us on Chatterly</a>
      </div>
      <article class="welcome">
        <h1>Welcome to Our Website Mainpage</h1>
        <p class="lead">Mauris vel lectus non libero porta tristique, integer placerat est luctus vehicula ut eget nisi.</p>
        <p>Lorem ipsum dolor sit amet, consectetur adipiscing elit. Sed viverra, tellus nec fermentum pretium, nulla magna vulputate arcu, vitae varius ante nunc sit amet lectus. Praesent suscipit orci quis justo tempor, id dictum nibh aliquet. Donec feugiat leo vel mauris luctus commodo.</p>
        <p>Curabitur tincidunt, ipsum at faucibus sagittis, arcu neque sodales mi, id ornare elit lorem non erat. Vestibulum ante ipsum primis in faucibus orci luctus et ultrices posuere cubilia curae. Integer posuere ligula eu quam tempus lacinia.</p>
        <p>Aliquam erat volutpat. Nam consequat feugiat lectus, sed pulvinar risus blandit sed. Phasellus at nunc non arcu interdum finibus vel at mi.</p>
      </article>
    </main>

    <aside class="side-col">
      <form class="consult">
        <h2>FREE CONSULTATION<span>Request</span></h2>
        <div class="field">First Name</div>
        <div class="field">Last Name</div>
        <div class="field">Phone Number</div>
        <div class="field area">Comments</div>
        <span class="btn-book">BOOK NOW</span>
      </form>

      <section class="panel">
        <h3>Office Hours</h3>
        <table class="hours">
          <tr><td>Monday:</td><td>8:00-11:00, 2:00-5:00</td></tr>
          <tr><td>Tuesday:</td><td>8:30-11:00, 2:00-5:30</td></tr>
          <tr><td>Wednesday:</td><td>8:00-11:00, 2:00-5:00</td></tr>
          <tr><td>Thursday:</td><td>10:00-12:00, 2:30-5:00</td></tr>
          <tr><td>Friday:</td><td>8:00-10:00, 1:00-5:00</td></tr>
          <tr><td>Saturday:</td><td>Closed</td></tr>
          <tr><td>Sunday:</td><td>Closed</td></tr>
        </table>
      </section>

      <section class="panel">
        <h3>Patient Testimonials</h3>
        <blockquote class="testimonial">
          "Lorem ipsum dolor sit amet, consectetur adipiscing elit. Cras porta velit eu nisi fringilla, sed tempus nulla dapibus. Quisque vel arcu ac turpis."
          <cite>- By Author Name</cite>
        </blockquote>
      </section>
    </aside>
  </div>
</div>

<footer>
  <div class="footer-band">
    <svg width="857" height="22" viewBox="0 0 857 22" preserveAspectRatio="none"><path d="M0 22 C250 0 600 0 857 22 Z" fill="#d9b87c"/></svg>
    <div class="footer-inner">
      <div class="footer-address"><strong>Fair Ridge Chiropractic</strong><br>4172 North Maple Blvd, Suite #7<br>Harlow Springs, FL 32990<br>555-014-2297</div>
      <div class="brand footer-brand"><span class="brand-mark"></span><span class="brand-name">FAIR RIDGE<br>CHIROPRACTIC</span></div>
    </div>
  </div>
  <div class="footer-bar">
    <div class="inner">
      <nav class="footer-nav">
        <a>Home</a><a>Why Fair Ridge?</a><a>How Chiropractic Helps</a><a>Ask the Doctor</a><a>Work Place Wellness</a><a>Request an Appointment</a><a>Blog</a><a>Contact Us</a>
      </nav>
      <div class="footer-row">
        <span>© 2014 Fair Ridge Chiropractic. All Rights Reserved.<br>Powered by Crestline Pixel Group</span>
        <div class="social"><span>Chatterly</span><span>Plexo+</span><span>Vidzio</span></div>
      </div>
    </div>
  </div>
</footer>
</body>
</html>
```